BRAMBLEFORD CONSTRUCTIONS B-Card

I currently have a b-card design but will be removing the image (tree) from the logo and have text only.
I want the card to be classy and strong within the building and construction industry.
I will be using Spot UV on the cards as per the attached examples. I will also send through some sketched ideas that I have in mind.
The color blue is similar to the image (No. 6) attached images

Target Market(s)

middle to maturre aged.
Home Owners / Renovators and Builders

Industry/Entity Type

Construction

Contact Information for Business Card

BRAMBLEFORD CONSTRUCTIONS
Name: Gareth Pennick
Title: Project Manager
Mobile: 0427 351 804
Office: (08) 9316 5172
Address: 47C Corvell Street, Malaga WA 6090
Email: info@bramblefordhomes.com.au
PO Box: 3817 Malaga WA 6944

Colors
0592cd
33a6d7
85cae6
1b1b1b

Requirements
Must have
• 1. It must have spot UV on the front of card, maybe back of card too
• 2. I really like the blue on image 6. (or at least a really cool electric blue against the charcoal grey background)
• 3. The font must be slimline and modern. Easy to read
• 4. There must be no black used on the card... Only greys and dark charcoal greys
• 5. Use only the text from the logo "Brambleford Constructions" Not the image of the tree. I am wanting the b-cards to be more masculine.
Nice to have
• 1. I like the design concept on image 6. but happy to see what else you can do with the Spot UV
• 2. Unless you have a really cool idea of the image of the tree (from previous logo) Spot UV somewhere in the design concept thats original and different then I am keen to see what you come up with
• 3. Try changing the color of the logo eg. full white or Blue and white
• 4. Another option is to have the Brambleford Logo on the front of card with the spot UV in the background of text which we specialise in eg, Roofing, Ceiling, Insulation, Gutter Guards, Electrical, Insurance etc and we can add or reduce items as required. Similar to image 12.
Should not have
• Do not include the image of the tree from previous logo. unless you have a really cool idea of Spot UV somewhere in the design concept thats original and different.

```html
<!DOCTYPE html>
<html lang="en">
<head>
<meta charset="utf-8">
<title>Brambleford Constructions – Business Card</title>
<link rel="stylesheet" href="https://fonts.googleapis.com/css2?family=Open+Sans:wght@300;400;600;700&display=swap">
<style>
  :root {
    --charcoal: #1f1f20;
    --charcoal-soft: #2b2b2d;
    --charcoal-leaf: #3a3a3d;
    --blue: #2ea5d9;
    --white: #ffffff;
    --page: #e9e9e7;
    --text-on-blue: #ffffff;
  }
  * { margin: 0; padding: 0; box-sizing: border-box; }
  html, body {
    width: 1200px;
    height: 900px;
    overflow: hidden;
  }
  body {
    background: var(--page);
    font-family: "Open Sans", Arial, sans-serif;
    position: relative;
  }
  .card {
    position: absolute;
    width: 525px;
    height: 300px;
    overflow: hidden;
    box-shadow: 0 6px 18px rgba(0,0,0,0.18);
  }
  .card--front { left: 50px; top: 300px; }
  .card--back  { left: 625px; top: 300px; }

  /* Front */
  .front-pattern {
    position: absolute;
    inset: 0;
    background: radial-gradient(ellipse at 50% 30%, var(--charcoal-leaf) 0%, var(--charcoal-soft) 45%, var(--charcoal) 100%);
  }

  /* Wordmark */
  .logo {
    position: absolute;
    left: 50%;
    transform: translateX(-50%);
    text-align: center;
    white-space: nowrap;
    font-weight: 700;
    line-height: 1;
    text-transform: uppercase;
  }
  .logo__name {
    display: block;
    font-size: 40px;
    letter-spacing: 0.5px;
  }
  .logo__sub {
    display: block;
    font-size: 14px;
    letter-spacing: 11.5px;
    margin-top: 7px;
    padding-left: 11.5px;
  }
  .card--front .logo { color: var(--white); top: 118px; }

  /* Back */
  .back-top {
    position: absolute;
    left: 0; top: 0;
    width: 100%;
    height: 168px;
    background: var(--charcoal);
  }
  .back-bottom {
    position: absolute;
    left: 0; top: 168px;
    width: 100%;
    height: 132px;
    background: var(--blue);
  }
  .card--back .logo { color: var(--blue); top: 62px; }

  .contact {
    position: absolute;
    left: 0; top: 186px;
    width: 100%;
    color: var(--text-on-blue);
    display: flex;
    justify-content: center;
    align-items: center;
  }
  .person {
    text-align: right;
    padding-right: 16px;
    border-right: 1px solid rgba(255,255,255,0.7);
  }
  .person__name {
    font-weight: 700;
    font-size: 17px;
    line-height: 1.15;
  }
  .person__title {
    font-weight: 400;
    font-size: 13px;
    line-height: 1.2;
  }
  .phones {
    padding-left: 16px;
    list-style: none;
    font-size: 12.5px;
    line-height: 1.45;
  }
  .phones li {
    display: flex;
    align-items: center;
    gap: 7px;
  }
  .phones svg { width: 11px; height: 11px; fill: var(--white); }

  .address {
    position: absolute;
    left: 0; top: 242px;
    width: 100%;
    text-align: center;
    color: var(--text-on-blue);
    font-size: 13px;
    line-height: 1.35;
  }
  .address strong { font-weight: 700; }
</style>
</head>
<body>

  <section class="card card--front" aria-label="Business card front">
    <div class="front-pattern" role="img" aria-label="Spot UV pattern of branching leaves over a charcoal background"></div>
    <div class="logo">
      <span class="logo__name">Brambleford</span>
      <span class="logo__sub">Constructions</span>
    </div>
  </section>

  <section class="card card--back" aria-label="Business card back">
    <div class="back-top"></div>
    <div class="back-bottom"></div>

    <div class="logo">
      <span class="logo__name">Brambleford</span>
      <span class="logo__sub">Constructions</span>
    </div>

    <div class="contact">
      <div class="person">
        <p class="person__name">Gareth Pennick</p>
        <p class="person__title">Project Manager</p>
      </div>
      <ul class="phones">
        <li>
          <svg viewBox="0 0 12 12" aria-hidden="true"><path d="M3.5 0h5a1 1 0 0 1 1 1v10a1 1 0 0 1-1 1h-5a1 1 0 0 1-1-1V1a1 1 0 0 1 1-1zm.3 1.3v8h4.4v-8zM6 9.8a.6.6 0 1 0 0 1.2.6.6 0 0 0 0-1.2z"/></svg>
          0427 351 804
        </li>
        <li>
          <svg viewBox="0 0 12 12" aria-hidden="true"><path d="M1 4.2C1 3 3 2 6 2s5 1 5 2.2v.8H8.5v-1c-.8-.3-1.6-.4-2.5-.4s-1.7.1-2.5.4v1H1zM3 6h6l1.5 4.5h-9z"/></svg>
          (08) 9316 5172
        </li>
      </ul>
    </div>

    <p class="address">
      47C Corvell Street, Carrowvale WA 6071<br>
      <strong>PO Box:</strong> 3817 Carrowvale WA 6943
    </p>
  </section>

</body>
</html>
```